Business card design Needed for new logo / Construction business, home extensions and new builds

We need a business card design using our new logo files which i will attach to this project :)

We are a small construction business specialising in home extensions, new builds and property development. We are very ambitious and would appreciate professional and elegant designs for our new business card.

Very serious about using the services on MakerQuarry and recently acquired our new logo from here :)

Please get involved, i will feedback when i can as i am very busy but can respond daily, thanks

Target Market(s)

People that want to build onto their houses, new building developments or adding too their existing property

Industry/Entity Type

Construction

Contact Information for Business Card

Renwick Tolliver Construction, Lionel Ashby (Managing Director), Tel 07822254961, email - info@renwick-tolliver, www.renwick-tolliver.co.uk

Colors

Designer to choose colors to be used in the design.

Requirements
Must have
• I like a deep grey on the back please. A lot of you have provided black from and back, try mixing things up a little. The black looks cool 😎 Thanks

```html
<!DOCTYPE html>
<html lang="en">
<head>
<meta charset="utf-8">
<title>Renwick Tolliver Construction – Business Card</title>
<link rel="stylesheet" href="https://fonts.googleapis.com/css2?family=Cinzel:wght@400&family=Open+Sans:wght@400;700&display=swap">
<style>
  :root {
    --page: #2a2a2d;
    --card-back-top: #2b2b2e;
    --card-back-bottom: #121214;
    --card-front: #1d1d20;
    --gold: #d9a531;
    --gold-light: #f2cf6a;
    --silver: #d6d6d6;
    --white: #f4f4f4;
  }
  * { box-sizing: border-box; margin: 0; padding: 0; }
  html, body { width: 1200px; height: 780px; overflow: hidden; }
  body {
    background: var(--page);
    display: flex;
    align-items: center;
    justify-content: center;
    gap: 40px;
    font-family: "Open Sans", Arial, sans-serif;
  }
  .card {
    width: 540px;
    height: 315px;
    position: relative;
    border-radius: 2px;
    box-shadow: 0 18px 40px rgba(0,0,0,.45);
    overflow: hidden;
  }
  .card-back {
    background: linear-gradient(160deg, var(--card-back-top), var(--card-back-bottom));
  }
  .card-back .pattern-area {
    position: absolute; inset: 0;
    background: linear-gradient(160deg, #3a3a3e 0%, #1a1a1c 55%, #101012 100%);
  }
  .card-back .back-brand {
    position: absolute; right: 26px; bottom: 24px;
    display: flex; align-items: center; gap: 8px;
    font-family: "Cinzel", Georgia, serif;
    font-size: 11px; letter-spacing: 1px;
    color: var(--silver);
  }
  .brand-square {
    width: 10px; height: 10px; background: var(--gold);
  }
  .card-front { background: var(--card-front); }
  .front-content {
    position: absolute; right: 30px; top: 30px;
    display: flex; flex-direction: column; align-items: flex-end;
  }
  .brand {
    display: flex; align-items: center; gap: 10px;
    font-family: "Cinzel", Georgia, serif;
    font-size: 17px; letter-spacing: 1.5px;
    color: var(--silver);
  }
  .brand .brand-square { width: 14px; height: 14px; }
  .holder {
    margin-top: 30px;
    display: flex; align-items: stretch; gap: 12px;
  }
  .holder-text { text-align: right; }
  .holder-name {
    font-size: 30px; font-weight: 700; line-height: 1.05;
  }
  .holder-name .first { color: var(--silver); }
  .holder-name .last { color: var(--gold); }
  .holder-role {
    font-size: 14px; color: var(--white); margin-top: 4px;
  }
  .gold-bar {
    width: 14px;
    background: linear-gradient(90deg, var(--gold), var(--gold-light), var(--gold));
  }
  .contacts {
    list-style: none;
    margin-top: 28px;
    margin-right: 2px;
  }
  .contacts li {
    display: flex; align-items: center; justify-content: flex-end; gap: 10px;
    font-size: 14px; color: var(--white); line-height: 24px;
  }
  .contacts svg { width: 13px; height: 13px; fill: var(--gold); }
</style>
</head>
<body>
  <section class="card card-back" aria-label="Card back">
    <div class="pattern-area" role="img" aria-label="Repeating brand-mark pattern in glossy black and silver tones"></div>
    <div class="back-brand"><span class="brand-square"></span>Renwick Tolliver Construction</div>
  </section>

  <section class="card card-front" aria-label="Card front">
    <div class="front-content">
      <div class="brand"><span class="brand-square"></span>Renwick Tolliver Construction</div>
      <div class="holder">
        <div class="holder-text">
          <p class="holder-name"><span class="first">Lionel</span> <span class="last">Ashby</span></p>
          <p class="holder-role">Managing Director</p>
        </div>
        <span class="gold-bar"></span>
      </div>
      <ul class="contacts">
        <li>0782 225 4961
          <svg viewBox="0 0 24 24" aria-hidden="true"><path d="M6.6 10.8a15.1 15.1 0 0 0 6.6 6.6l2.2-2.2a1 1 0 0 1 1-.25 11.4 11.4 0 0 0 3.6.57 1 1 0 0 1 1 1V20a1 1 0 0 1-1 1A17 17 0 0 1 3 4a1 1 0 0 1 1-1h3.5a1 1 0 0 1 1 1c0 1.25.2 2.45.57 3.6a1 1 0 0 1-.25 1z"/></svg>
        </li>
        <li>info@renwick-tolliver.co.uk
          <svg viewBox="0 0 24 24" aria-hidden="true"><path d="M3 5h18a1 1 0 0 1 1 1v12a1 1 0 0 1-1 1H3a1 1 0 0 1-1-1V6a1 1 0 0 1 1-1zm9 7.2L4 7.5V17h16V7.5z"/></svg>
        </li>
        <li>www.renwick-tolliver.co.uk
          <svg viewBox="0 0 24 24" aria-hidden="true"><path d="M12 2a10 10 0 1 0 0 20 10 10 0 0 0 0-20zm6.9 6h-2.9a15.7 15.7 0 0 0-1.4-3.6A8 8 0 0 1 18.9 8zM12 4c.8 1.2 1.5 2.5 1.9 4h-3.8c.4-1.5 1.1-2.8 1.9-4zM4.3 14a8 8 0 0 1 0-4h3.4a16.5 16.5 0 0 0 0 4zm.8 2h2.9c.3 1.3.8 2.5 1.4 3.6A8 8 0 0 1 5.1 16zM8 8H5.1a8 8 0 0 1 4.3-3.6C8.8 5.5 8.3 6.7 8 8zm4 12c-.8-1.2-1.5-2.5-1.9-4h3.8c-.4 1.5-1.1 2.8-1.9 4zm2.3-6H9.7a14.7 14.7 0 0 1 0-4h4.6a14.7 14.7 0 0 1 0 4zm.3 5.6c.6-1.1 1.1-2.3 1.4-3.6h2.9a8 8 0 0 1-4.3 3.6zm1.7-5.6a16.5 16.5 0 0 0 0-4h3.4a8 8 0 0 1 0 4z"/></svg>
        </li>
      </ul>
    </div>
  </section>
</body>
</html>
```